Working Capital graphics

Our business advisory firm requires 9 images to be re-created and improved in the branding of our business.

The 9 images have been uploaded below and the colours and branding of the business can be found at the website www.tallowmereadvisory.com.au

```html
<!DOCTYPE html>
<html lang="en">
<head>
<meta charset="utf-8">
<title>Working Capital</title>
<link rel="stylesheet" href="https://fonts.googleapis.com/css2?family=Open+Sans:wght@700&display=swap">
<style>
  :root {
    --sky: #0cb1f2;
    --sky-ring: #10b0ee;
    --navy: #0e3a8a;
    --ink: #2e2b8c;
    --paper: #ffffff;
  }
  html, body {
    margin: 0;
    padding: 0;
    width: 1200px;
    height: 1200px;
    overflow: hidden;
    background: var(--paper);
  }
  .diagram {
    display: block;
    width: 1200px;
    height: 1200px;
    font-family: "Open Sans", Arial, sans-serif;
    font-weight: 700;
  }
  .hub-core { fill: var(--sky); }
  .hub-ring { fill: none; stroke: var(--navy); stroke-width: 13; }
  .spoke { stroke: var(--navy); stroke-width: 17; }
  .node { fill: var(--paper); stroke: var(--sky-ring); stroke-width: 13; }
  .joint-outer { fill: var(--paper); }
  .joint-inner { fill: var(--navy); }
  .node-label {
    fill: var(--ink);
    font-size: 28px;
    text-anchor: middle;
    dominant-baseline: central;
    letter-spacing: 0.3px;
  }
  .hub-label {
    fill: var(--paper);
    font-size: 60px;
    text-anchor: middle;
    dominant-baseline: central;
    letter-spacing: 1px;
  }
</style>
</head>
<body>
<svg class="diagram" viewBox="0 0 1500 1500" xmlns="http://www.w3.org/2000/svg" aria-label="Working capital drivers diagram">
  <g class="spokes">
    <line class="spoke" x1="745" y1="468" x2="747" y2="282"/>
    <line class="spoke" x1="941" y1="543" x2="1065" y2="396"/>
    <line class="spoke" x1="1030" y1="720" x2="1225" y2="712"/>
    <line class="spoke" x1="979" y1="940" x2="1151" y2="1029"/>
    <line class="spoke" x1="838" y1="1044" x2="886" y2="1229"/>
    <line class="spoke" x1="632" y1="1031" x2="551" y2="1206"/>
    <line class="spoke" x1="484" y1="901" x2="308" y2="982"/>
    <line class="spoke" x1="454" y1="690" x2="268" y2="672"/>
    <line class="spoke" x1="550" y1="527" x2="418" y2="388"/>
  </g>

  <circle class="hub-ring" cx="740" cy="762" r="295"/>
  <circle class="hub-core" cx="740" cy="762" r="240"/>
  <text class="hub-label" x="745" y="729">WORKING</text>
  <text class="hub-label" x="745" y="799">CAPITAL</text>

  <g class="nodes">
    <circle class="node" cx="747" cy="282" r="122"/>
    <circle class="node" cx="1065" cy="396" r="122"/>
    <circle class="node" cx="1225" cy="712" r="122"/>
    <circle class="node" cx="1151" cy="1029" r="122"/>
    <circle class="node" cx="886" cy="1229" r="122"/>
    <circle class="node" cx="551" cy="1206" r="122"/>
    <circle class="node" cx="308" cy="982" r="122"/>
    <circle class="node" cx="268" cy="672" r="122"/>
    <circle class="node" cx="418" cy="388" r="122"/>
  </g>

  <g class="joints">
    <g transform="translate(745 468)"><circle class="joint-outer" r="15"/><circle class="joint-inner" r="10"/></g>
    <g transform="translate(941 543)"><circle class="joint-outer" r="15"/><circle class="joint-inner" r="10"/></g>
    <g transform="translate(1030 720)"><circle class="joint-outer" r="15"/><circle class="joint-inner" r="10"/></g>
    <g transform="translate(979 940)"><circle class="joint-outer" r="15"/><circle class="joint-inner" r="10"/></g>
    <g transform="translate(838 1044)"><circle class="joint-outer" r="15"/><circle class="joint-inner" r="10"/></g>
    <g transform="translate(632 1031)"><circle class="joint-outer" r="15"/><circle class="joint-inner" r="10"/></g>
    <g transform="translate(484 901)"><circle class="joint-outer" r="15"/><circle class="joint-inner" r="10"/></g>
    <g transform="translate(454 690)"><circle class="joint-outer" r="15"/><circle class="joint-inner" r="10"/></g>
    <g transform="translate(550 527)"><circle class="joint-outer" r="15"/><circle class="joint-inner" r="10"/></g>
  </g>

  <g class="labels">
    <text class="node-label" x="745" y="238">Supply</text>
    <text class="node-label" x="745" y="285">Chain</text>
    <text class="node-label" x="745" y="332">Issues</text>

    <text class="node-label" x="1065" y="378">Process</text>
    <text class="node-label" x="1065" y="425">Issues</text>

    <text class="node-label" x="1225" y="690">Forecasting</text>
    <text class="node-label" x="1225" y="737">and Planning</text>

    <text class="node-label" x="1151" y="1004">Customer</text>
    <text class="node-label" x="1151" y="1051">Management</text>

    <text class="node-label" x="886" y="1207">SKU</text>
    <text class="node-label" x="886" y="1254">Complexity</text>

    <text class="node-label" x="551" y="1186">Supplier</text>
    <text class="node-label" x="551" y="1233">Management</text>

    <text class="node-label" x="308" y="961">KPIs and</text>
    <text class="node-label" x="308" y="1008">Measures</text>

    <text class="node-label" x="268" y="628">IT Systems</text>
    <text class="node-label" x="268" y="675">and</text>
    <text class="node-label" x="268" y="722">Information</text>

    <text class="node-label" x="416" y="361">Terms and</text>
    <text class="node-label" x="416" y="408">Conditions</text>
  </g>
</svg>
</body>
</html>
```